Non fiction leadership Book Cover design needed for “Stay Bold: Build On Lasting Discipline”

I need a front cover design for a new book 6 X 9 traditional non-fiction book.

Title: "Stay BOLD - Build On Lasting Discipline"

The subtitle is not finalized- so use 2 lines of smaller dummy text

My brand guide is attached (please use the tan color sparingly)

I'd like to see BOLD look like it is in motion and "flying" across the page

Need CREATIVE designs and options

Do not want my picture on the front cover - I do want it on the back cover.

On the front cover I’d like to see creative use of font to create movement on “BOLD”

Target Market(s)

Business leaders

Industry/Entity Type

Aviation

Font styles to use
Other font styles liked:
• See style guide- can add additional font (modern script or san serif)

Colors
0054AA
0677BA
7BADD7
CADEEF
E8F1F8
EB3D1F
EC4F4E
F09395
F8D3D4
FCEDEE

Requirements
Must have
• Creative font use, using perspective to create movement/motion on BOLD
Should not have
• My picture on the front cover- my picture should be on the back cover

```html
<!DOCTYPE html>
<html lang="en">
<head>
<meta charset="utf-8">
<title>Stay Bold: Build On Lasting Discipline</title>
<link rel="stylesheet" href="https://fonts.googleapis.com/css2?family=Montserrat:wght@600;700&family=Bebas+Neue&display=swap">
<style>
  :root {
    --bg-top: #ec5150;
    --bg-mid: #ef8585;
    --bg-bottom: #f7d2d2;
    --band-red: #d81f27;
    --band-dark: #9e1b2d;
    --band-bright: #e91d25;
    --ink-white: #ffffff;
    --ink-black: #0b0b0b;
  }
  * { margin: 0; padding: 0; box-sizing: border-box; }
  html, body { width: 800px; height: 1200px; overflow: hidden; background: #ffffff; }
  .cover {
    position: relative;
    width: 800px;
    height: 1200px;
    overflow: hidden;
    background:
      radial-gradient(ellipse 520px 420px at 400px 1200px, rgba(250,224,224,0.9), rgba(250,224,224,0) 100%),
      linear-gradient(180deg, var(--bg-top) 0%, #e6645e 30%, var(--bg-mid) 50%, #f2a7a7 72%, var(--bg-bottom) 100%);
    font-family: "Montserrat", Arial, sans-serif;
    color: var(--ink-white);
  }
  .title-lead {
    position: absolute;
    top: 28px;
    left: 0;
    width: 800px;
    text-align: center;
    font-weight: 700;
    font-size: 232px;
    line-height: 1;
    letter-spacing: -4px;
  }
  .motion-band {
    position: absolute;
    top: 0;
    left: 0;
    width: 800px;
    height: 600px;
  }
  .motion-word text {
    font-family: "Montserrat", Arial, sans-serif;
    font-weight: 600;
    font-size: 128px;
    fill: var(--ink-white);
  }
  .title-key {
    position: absolute;
    top: 516px;
    left: 0;
    width: 800px;
    display: flex;
    justify-content: center;
    align-items: center;
    gap: 30px;
    font-weight: 700;
    font-size: 140px;
    line-height: 1;
    letter-spacing: -2px;
  }
  .title-key .dash {
    display: block;
    width: 41px;
    height: 19px;
    background: var(--ink-white);
    margin-top: 24px;
  }
  .title-rest {
    position: absolute;
    top: 664px;
    left: 0;
    width: 800px;
    text-align: center;
    font-weight: 700;
    font-size: 58px;
    line-height: 1;
    letter-spacing: -1px;
    white-space: nowrap;
  }
  .subtitle {
    position: absolute;
    top: 824px;
    left: 0;
    width: 800px;
    text-align: center;
    font-family: "Bebas Neue", "Arial Narrow", sans-serif;
    font-size: 48px;
    line-height: 57px;
    letter-spacing: 0.19em;
    color: var(--ink-black);
  }
  .rule {
    position: absolute;
    top: 991px;
    left: 324px;
    width: 152px;
    height: 11px;
    background: var(--ink-white);
  }
  .author {
    position: absolute;
    top: 1074px;
    left: 0;
    width: 800px;
    text-align: center;
    font-family: "Bebas Neue", "Arial Narrow", sans-serif;
    font-size: 66px;
    line-height: 1;
    letter-spacing: 0.16em;
    color: var(--ink-black);
  }
</style>
</head>
<body>
  <main class="cover">
    <h1 class="title-lead">STAY</h1>

    <svg class="motion-band" viewBox="0 0 800 600" aria-hidden="true">
      <defs>
        <linearGradient id="bandFill" x1="0" y1="0" x2="1" y2="0.25">
          <stop offset="0" stop-color="var(--band-red)"/>
          <stop offset="0.4" stop-color="var(--band-dark)"/>
          <stop offset="0.7" stop-color="#b91f2b"/>
          <stop offset="1" stop-color="var(--band-bright)"/>
        </linearGradient>
      </defs>
      <path class="band-shape" fill="url(#bandFill)"
        d="M0 282 C40 277 70 275 102 276 C180 279 250 296 306 316 C380 343 450 362 510 372 C560 381 600 389 650 390 C720 391 770 384 800 375
           L800 526 C760 531 710 534 663 533 C610 530 560 522 510 510 C440 494 370 476 306 459 C240 440 170 418 102 418 C60 418 30 422 0 428 Z"/>
      <g class="motion-word">
        <text transform="translate(170 407) rotate(14)">B</text>
        <text transform="translate(293 440) rotate(10)">O</text>
        <text transform="translate(425 480) rotate(6)">L</text>
        <text transform="translate(530 505) rotate(2)">D</text>
      </g>
    </svg>

    <div class="title-key"><span class="dash"></span><span class="word">Build</span><span class="dash"></span></div>
    <p class="title-rest">On Lasting Discipline</p>

    <p class="subtitle">Unlock your inner potential<br>and soar to new heights</p>

    <div class="rule"></div>

    <p class="author">Author Name</p>
  </main>
</body>
</html>
```